Business Card Update, need to bring life to the card, two sided color

We need a new business card design, are moving and changing addresses and need a new look, we have the logos already attached but need a new style moving forward. Can incorporate the color of the logo (The Green) as well, maybe a solid back? We deal with safety products revolving around static electricity and safety lighting. Would like to keep same font in second logo as well.

Target Market(s)

Electrical Safety, Lighting

Contact Information for Business Card

Dale Fenwick
Vice President
Office: 770-555-4821
Cell: 770-555-3067
dale@tkfenwick.example
www.tkfenwick.example
4700 West Harbor Boulevard
Suite #150
Roswell, GA 30076

Font styles to use
Serif
Sans Serif

Requirements
Must have
• Since 1918
Nice to have
• Could use the 100 Year Logo for back of card, would like the back of card to be the same green as logo.
Should not have
• No black cards please.

```html
<!DOCTYPE html>
<html lang="en">
<head>
<meta charset="utf-8">
<title>T.K. Fenwick — Business Card</title>
<link rel="stylesheet" href="https://fonts.googleapis.com/css2?family=Open+Sans:wght@400;700&display=swap">
<style>
  :root{
    --brand-green:#0b9a55;
    --card-white:#ffffff;
    --text-grey:#6d6d6d;
    --divider:#bdbdbd;
    --canvas:#e9eaea;
  }
  *{margin:0;padding:0;box-sizing:border-box}
  html,body{width:1200px;height:768px;overflow:hidden;background:var(--canvas)}
  body{font-family:"Open Sans",Arial,sans-serif;position:relative}
  .card{position:absolute;top:234px;width:525px;height:300px;border-radius:22px;overflow:hidden;box-shadow:0 4px 14px rgba(0,0,0,.12)}
  .card--back{left:50px;background:var(--brand-green);color:var(--card-white)}
  .card--front{left:625px;background:var(--card-white)}

  /* back */
  .back-mark{position:absolute;left:0;right:0;top:66px;display:flex;flex-direction:column;align-items:center;gap:10px}
  .back-mark__circle{width:88px;height:88px;border-radius:50%;background:var(--card-white)}
  .back-mark__name{font-weight:700;font-size:22px;line-height:1.1;color:var(--card-white)}
  .back-mark__since{font-size:13px;letter-spacing:2px;margin-top:-6px}
  .back-web{position:absolute;left:0;right:0;bottom:34px;text-align:center;font-size:13px;letter-spacing:4px}

  /* front */
  .brand{position:absolute;left:170px;width:320px;top:22px;text-align:center;color:var(--brand-green);font-weight:700}
  .brand__circle{width:62px;height:62px;border-radius:50%;background:var(--brand-green);margin:0 auto 6px}
  .brand__name{font-size:30px;line-height:1.05}
  .brand__sub{font-size:13px;line-height:1.3}

  .person{position:absolute;right:282px;top:160px;text-align:right;color:var(--text-grey)}
  .person__name{color:var(--brand-green);font-weight:700;font-size:23px;line-height:1.15}
  .person__title{font-size:16px;line-height:1.3}
  .person__address{font-size:14px;line-height:1.4}

  .divider{position:absolute;left:262px;top:164px;width:1px;height:116px;background:var(--divider)}

  .contact{position:absolute;left:276px;top:170px;list-style:none;color:var(--text-grey);font-size:14px}
  .contact li{display:flex;align-items:center;gap:9px;height:21px}
  .contact svg{width:13px;height:13px;flex:none;fill:var(--brand-green)}
</style>
</head>
<body>

<section class="card card--back" aria-label="Card back">
  <div class="back-mark">
    <div class="back-mark__circle"></div>
    <div class="back-mark__name">T.K. Fenwick</div>
    <div class="back-mark__since">SINCE 1918</div>
  </div>
  <div class="back-web">www.tkfenwick.example</div>
</section>

<section class="card card--front" aria-label="Card front">
  <div class="brand">
    <div class="brand__circle"></div>
    <div class="brand__name">T.K. Fenwick</div>
    <div class="brand__sub">Manufacturing Company, Inc.</div>
  </div>

  <div class="person">
    <div class="person__name">Dale Fenwick</div>
    <div class="person__title">Vice President</div>
    <div class="person__address">4700 West Harbor Boulevard<br>Suite #150<br>Roswell, GA 30076</div>
  </div>

  <div class="divider"></div>

  <ul class="contact">
    <li><svg viewBox="0 0 16 16" aria-hidden="true"><path d="M3 1h3l1.5 4-2 1.3a9 9 0 0 0 4.2 4.2L11 8.5l4 1.5v3a2 2 0 0 1-2 2A12 12 0 0 1 1 3a2 2 0 0 1 2-2z"/></svg>770 555 4821</li>
    <li><svg viewBox="0 0 16 16" aria-hidden="true"><path d="M4 0h8a1 1 0 0 1 1 1v14a1 1 0 0 1-1 1H4a1 1 0 0 1-1-1V1a1 1 0 0 1 1-1zm1 2v10h6V2z"/></svg>770 555 3067</li>
    <li><svg viewBox="0 0 16 16" aria-hidden="true"><path d="M4 1h8v4H4zM1 6h14v7h-3v2H4v-2H1zm4 5v3h6v-3z"/></svg>770 555 7712</li>
    <li><svg viewBox="0 0 16 16" aria-hidden="true"><path d="M1 3h14v10H1zm1.5 1.2L8 8.5l5.5-4.3z"/></svg>dale@tkfenwick.example</li>
    <li><svg viewBox="0 0 16 16" aria-hidden="true"><path d="M8 0a8 8 0 1 1 0 16A8 8 0 0 1 8 0zm0 1.5a6.5 6.5 0 0 0-1 12.9V12L5 10V7h4l2 2v3.5A6.5 6.5 0 0 0 8 1.5z"/></svg>www.tkfenwick.example</li>
  </ul>
</section>

</body>
</html>
```